Oil and Gas Exploration and Production company needs a business card design

We need a business card design using our logo and colors in the logo. We want a mainstream design.

```html
<!DOCTYPE html>
<html lang="en">
<head>
<meta charset="utf-8">
<title>Valora Oil &amp; Gas – Business Card</title>
<link rel="stylesheet" href="https://fonts.googleapis.com/css2?family=Arvo:wght@700&family=Roboto:wght@400;700&family=Roboto+Condensed:wght@400&display=swap">
<style>
  :root {
    --bg: #e6e2da;
    --paper: #ffffff;
    --ink: #1c1b1a;
    --gold: #c8992b;
    --grey-text: #4a4a4a;
    --rule: #b9b9b9;
  }
  * { box-sizing: border-box; margin: 0; padding: 0; }
  html, body { width: 1200px; height: 911px; overflow: hidden; background: var(--bg); }
  .canvas { position: relative; width: 1200px; height: 911px; }

  .card {
    position: absolute;
    width: 540px; height: 309px;
    border-radius: 16px;
    overflow: hidden;
    box-shadow: 0 6px 18px rgba(0,0,0,0.18);
  }

  /* Front */
  .card-front { left: 40px; top: 301px; background: var(--paper); }
  .brand {
    position: absolute; left: 210px; top: 58px;
    display: flex; align-items: center; gap: 12px;
    white-space: nowrap;
  }
  .brand-dot { width: 34px; height: 34px; border-radius: 50%; background: var(--gold); flex: none; }
  .brand-name {
    font-family: "Arvo", serif; font-weight: 700;
    font-size: 30px; color: var(--ink); letter-spacing: 0.5px;
  }
  .brand-rule {
    position: absolute; left: 210px; top: 122px; width: 300px; height: 1px; background: var(--rule);
  }
  .holder { position: absolute; left: 36px; top: 168px; }
  .holder-name {
    font-family: "Roboto", sans-serif; font-weight: 700; font-size: 17px;
    color: var(--ink); letter-spacing: 0.3px;
  }
  .holder-title {
    font-family: "Roboto", sans-serif; font-size: 12.5px; color: var(--gold); margin-top: 2px;
  }
  .holder-rule { width: 170px; height: 1px; background: var(--rule); margin: 8px 0 7px; }
  .contact-list { list-style: none; }
  .contact-list li {
    display: flex; align-items: center; gap: 8px;
    font-family: "Roboto Condensed", sans-serif; font-size: 12.5px;
    color: var(--grey-text); line-height: 16px;
    white-space: nowrap;
  }
  .contact-list svg { width: 10px; height: 10px; fill: var(--ink); flex: none; }

  .address {
    position: absolute; right: 34px; top: 200px; text-align: right;
    font-family: "Roboto Condensed", sans-serif; font-size: 12.5px;
    color: var(--grey-text); line-height: 16px;
    white-space: nowrap;
  }
  .edge-tab { position: absolute; left: 0; top: 246px; width: 9px; height: 22px; background: var(--ink); }
  .gold-band { position: absolute; left: 0; bottom: 0; width: 330px; height: 9px; background: var(--gold); }
  .web-bar {
    position: absolute; right: 0; bottom: 0; width: 216px; height: 30px;
    background: var(--ink); border-top-left-radius: 4px;
    display: flex; align-items: center; justify-content: flex-end; padding-right: 22px;
    font-family: "Roboto", sans-serif; font-size: 12px; color: #fff; letter-spacing: 1px;
    white-space: nowrap;
  }

  /* Back */
  .card-back { left: 620px; top: 301px; background: var(--gold); }
  .back-web {
    position: absolute; left: 30px; top: 28px;
    font-family: "Roboto", sans-serif; font-size: 11.5px; color: #fff; letter-spacing: 4px;
    white-space: nowrap;
  }
  .back-mark {
    position: absolute; left: 50%; top: 54%; transform: translate(-50%, -50%);
    display: flex; align-items: center; gap: 12px;
    white-space: nowrap;
  }
  .back-dot { width: 46px; height: 46px; border-radius: 50%; background: var(--ink); flex: none; }
  .back-name {
    font-family: "Arvo", serif; font-weight: 700; font-size: 26px; color: var(--ink);
  }
</style>
</head>
<body>
<main class="canvas">

  <section class="card card-front" aria-label="Business card front">
    <div class="brand">
      <span class="brand-dot"></span>
      <span class="brand-name">Valora Oil &amp; Gas</span>
    </div>
    <div class="brand-rule"></div>

    <div class="holder">
      <p class="holder-name">DANIEL HARPER</p>
      <p class="holder-title">CEO/FOUNDER</p>
      <div class="holder-rule"></div>
      <ul class="contact-list">
        <li><svg viewBox="0 0 10 10"><path d="M2 0.5l2 2-1 1.2c.6 1.3 1.4 2.1 2.7 2.7l1.2-1 2 2-1.3 1.6C4.5 8.7 1.2 5.4.4 1.8z"/></svg>555 210 4471</li>
        <li><svg viewBox="0 0 10 10"><path d="M2.5 0h5v10h-5zM3.3 1v7h3.4V1z" fill-rule="evenodd"/></svg>555 318 2206</li>
        <li><svg viewBox="0 0 10 10"><path d="M1 3h8v7H1zM3 0h4v3H3z"/></svg>555 904 6632</li>
        <li><svg viewBox="0 0 10 10"><path d="M0 0h10v10H0zM2 5.2l.9-.9 1.4 1.4 2.8-2.9.9.9-3.7 3.8z" fill-rule="evenodd"/></svg>info@valoraenergy.com</li>
      </ul>
    </div>

    <p class="address">1420 Birchwood Road<br>Cedarbrook, Montana 59870</p>

    <div class="edge-tab"></div>
    <div class="gold-band"></div>
    <div class="web-bar">www.valoraenergy.com</div>
  </section>

  <section class="card card-back" aria-label="Business card back">
    <p class="back-web">www.valoraenergy.com</p>
    <div class="back-mark">
      <span class="back-dot"></span>
      <span class="back-name">Valora Oil &amp; Gas</span>
    </div>
  </section>

</main>
</body>
</html>
```